Volbrey Inc Business Card

Looking to get an updated business card for a Contract Machining company (www.volbreyinc.example) - looking for a clean design the portrays the technical nature of the business - colors can follow the website design and be in any combination that makes sense (red black, white, metallic or silver) - logos attached for use also. Would like space for: Name, title, business phone (555 214-3086), cell phone , website (www.volbreyinc.example) - possibly QR code could be integrated for website (designer choice), business address - 418 Harlow Bend, Elmsbury, WA 48199 (cards will be for 4 employees, I will either need to modify a template or I can provide individual information)
Target Market(s)
Aerospace, defense and medical device manufacturing companies that need machining
Industry/Entity Type
Machining for aerospace, defense, medical
Contact Information for Business Card
Name, Title, Business Phone, Cell Phone, email, business website and business address
Look and feel

```html
<!DOCTYPE html>
<html lang="en">
<head>
<meta charset="utf-8">
<title>Volbrey Inc Business Card</title>
<link rel="stylesheet" href="https://fonts.googleapis.com/css2?family=Poppins:wght@400;600;700&display=swap">
<style>
  :root {
    --brand-red: #b31f25;
    --ink: #1d1d1d;
    --paper: #ffffff;
    --backdrop: #2c2c2c;
    --divider: #b9b9b9;
  }
  * { box-sizing: border-box; margin: 0; padding: 0; }
  html, body {
    width: 1093px;
    height: 1200px;
    overflow: hidden;
    background: var(--backdrop);
    font-family: "Poppins", sans-serif;
  }
  .canvas { position: relative; width: 1093px; height: 1200px; }

  .card {
    position: absolute;
    border-radius: 26px;
    box-shadow: 2px 3px 4px rgba(0,0,0,0.55);
  }
  .card-front { left: 265px; top: 226px; width: 577px; height: 356px; background: var(--paper); }
  .card-back  { left: 265px; top: 621px; width: 581px; height: 356px; background: var(--brand-red); }

  .brand-mark {
    position: absolute;
    left: 95px; top: 78px;
    width: 151px; height: 151px;
    border-radius: 50%;
    background: var(--brand-red);
  }
  .brand-name {
    position: absolute;
    left: 60px; top: 234px;
    width: 221px;
    text-align: center;
    color: var(--brand-red);
    font-weight: 700;
    font-size: 22px;
    letter-spacing: 0.3px;
    line-height: 1;
    white-space: nowrap;
  }

  .divider {
    position: absolute;
    left: 284px; top: 74px;
    width: 1.5px; height: 209px;
    background: linear-gradient(to bottom, rgba(185,185,185,0), var(--divider) 20%, var(--divider) 80%, rgba(185,185,185,0));
  }

  .details { position: absolute; left: 311px; top: 79px; color: var(--ink); }
  .person-name {
    color: var(--brand-red);
    font-weight: 700;
    font-size: 21.5px;
    line-height: 22px;
    letter-spacing: 0.2px;
    white-space: nowrap;
  }
  .person-title { font-size: 17px; line-height: 20px; }

  .contact-list { list-style: none; margin-top: 13px; }
  .contact-list li {
    display: flex;
    align-items: center;
    gap: 7px;
    font-size: 17px;
    line-height: 21px;
    white-space: nowrap;
  }
  .contact-list svg { width: 15px; height: 15px; flex: none; fill: var(--brand-red); }
  .web-highlight { color: var(--brand-red); }

  .address { margin-top: 13px; font-size: 17px; line-height: 21px; white-space: nowrap; }

  .back-name {
    position: absolute;
    left: 0; right: 0; top: 128px;
    text-align: center;
    color: var(--paper);
    font-weight: 700;
    font-size: 84px;
    line-height: 1;
    letter-spacing: 1px;
  }
</style>
</head>
<body>
<div class="canvas">

  <section class="card card-front">
    <div class="brand-mark" aria-hidden="true"></div>
    <div class="brand-name">VOLBREY INC</div>

    <div class="divider"></div>

    <div class="details">
      <h1 class="person-name">DANIEL HARTWELL</h1>
      <p class="person-title">Managing Director</p>

      <ul class="contact-list">
        <li>
          <svg viewBox="0 0 24 24" aria-hidden="true"><path d="M6.6 10.8a15.1 15.1 0 0 0 6.6 6.6l2.2-2.2a1 1 0 0 1 1-.25 11.4 11.4 0 0 0 3.6.57 1 1 0 0 1 1 1V20a1 1 0 0 1-1 1A17 17 0 0 1 3 4a1 1 0 0 1 1-1h3.5a1 1 0 0 1 1 1c0 1.250.2 2.46.57 3.6a1 1 0 0 1-.25 1z"/></svg>
          555 214-3086
        </li>
        <li>
          <svg viewBox="0 0 24 24" aria-hidden="true"><path d="M7 1h10a2 2 0 0 1 2 2v18a2 2 0 0 1-2 2H7a2 2 0 0 1-2-2V3a2 2 0 0 1 2-2zm0 3v14h10V4zm5 15.2a1.2 1.2 0 1 0 0 2.4 1.2 1.2 0 0 0 0-2.4z"/></svg>
          555 730-4417
        </li>
        <li>
          <svg viewBox="0 0 24 24" aria-hidden="true"><path d="M2 5h20v14H2zm2 2v.5l8 5.5 8-5.5V7l-8 5.5z"/></svg>
          info@volbreyinc.example
        </li>
        <li>
          <svg viewBox="0 0 24 24" aria-hidden="true"><path d="M12 2a10 10 0 1 0 0 20 10 10 0 0 0 0-20zm6.9 6h-2.9a15.6 15.6 0 0 0-1.4-3.6A8 8 0 0 1 18.9 8zM12 4c.8 1.2 1.5 2.5 1.9 4h-3.8c.4-1.5 1.1-2.8 1.9-4zM4.3 14a8 8 0 0 1 0-4h3.4a16 16 0 0 0 0 4zm.8 2h2.9c.3 1.3.8 2.5 1.4 3.6A8 8 0 0 1 5.1 16zM8 8H5.1a8 8 0 0 1 4.3-3.6C8.8 5.5 8.3 6.7 8 8zm4 12c-.8-1.2-1.5-2.5-1.9-4h3.8c-.4 1.5-1.1 2.8-1.9 4zm2.3-6H9.7a14 14 0 0 1 0-4h4.6a14 14 0 0 1 0 4zm.3 5.6c.6-1.1 1.1-2.3 1.4-3.6h2.9a8 8 0 0 1-4.3 3.6zm1.7-5.6a16 16 0 0 0 0-4h3.4a8 8 0 0 1 0 4z"/></svg>
          <span>www.<span class="web-highlight">volbreyinc</span>.example</span>
        </li>
      </ul>

      <p class="address">418 Harlow Bend,<br>Elmsbury, WA 48199</p>
    </div>
  </section>

  <section class="card card-back">
    <div class="back-name">VOLBREY</div>
  </section>

</div>
</body>
</html>
```